BQR, LLC Original

I need a business card design for a new company in Gaithersburg, MD. Though the name of the company is Wiremasters Of Northfield (BQR) we specialize in commercial kitchen ventilation systems as a complete turnkey project or as a service provider. We can design the entire system including the hoods, fans, ductwork, and fire system. We also specialize in fire alarm service, design, install and inspection. We are experts on any Ventaro Dynamics equipment including Pulsar VXM, Pulsar Canopies, EMS controls, Standard controls, PCU filtration and Make-up Air units with heaters and cooling. We can repair/retrofit old water wash hood systems as well. We are experts with local code requirements and upgrades.

Industry/Entity Type

Business

Contact Information for Business Card

Dale Pruitt, Wiremasters Of Northfield, LLC; 240-555-0187 Cell, Fairhaven, MD 20811. Dalep@wiremastersnorthfield.example

```html
<!DOCTYPE html>
<html lang="en">
<head>
<meta charset="utf-8">
<title>Of Northfield, LLC — Business Card</title>
<link href="https://fonts.googleapis.com/css2?family=Abril+Fatface&family=Arimo:wght@400&display=swap" rel="stylesheet">
<style>
  :root {
    --page-bg: #ece9e4;
    --card-yellow: #f8f08c;
    --card-yellow-deep: #f5e96e;
    --card-white: #ffffff;
    --ink: #111111;
    --shadow: rgba(0, 0, 0, 0.18);
  }
  * { box-sizing: border-box; margin: 0; padding: 0; }
  html, body {
    width: 1200px;
    height: 914px;
    overflow: hidden;
    background: var(--page-bg);
  }
  .sheet {
    width: 1200px;
    height: 914px;
    display: flex;
    align-items: center;
    justify-content: center;
    gap: 40px;
  }
  .card {
    position: relative;
    width: 540px;
    height: 309px;
    box-shadow: 0 6px 18px var(--shadow);
    overflow: hidden;
  }
  .company-name {
    font-family: "Abril Fatface", "Bodoni Moda", serif;
    font-weight: 400;
    color: var(--ink);
    white-space: nowrap;
    letter-spacing: 0.5px;
  }

  /* Front */
  .card--front {
    background: linear-gradient(120deg, var(--card-yellow) 0%, var(--card-yellow-deep) 100%);
    display: flex;
    align-items: center;
    justify-content: center;
  }
  .card--front .company-name { font-size: 44px; }

  /* Back */
  .card--back { background: var(--card-white); }
  .back__band {
    position: absolute;
    left: 0; top: 0;
    width: 100%;
    height: 112px;
    background: linear-gradient(120deg, var(--card-yellow) 0%, var(--card-yellow-deep) 100%);
    display: flex;
    align-items: flex-end;
    justify-content: center;
    padding-bottom: 16px;
  }
  .back__band .company-name { font-size: 42px; line-height: 1; }

  .contact-list {
    position: absolute;
    left: 32px;
    top: 180px;
    list-style: none;
    font-family: "Arimo", Arial, sans-serif;
    font-size: 15px;
    color: var(--ink);
  }
  .contact-list li {
    display: flex;
    align-items: center;
    gap: 10px;
    height: 22px;
  }
  .contact-list svg { width: 14px; height: 14px; flex: none; }

  .person {
    position: absolute;
    right: 34px;
    top: 196px;
    text-align: right;
    font-family: "Arimo", Arial, sans-serif;
    color: var(--ink);
  }
  .person__name { font-size: 20px; line-height: 1.15; }
  .person__role { font-size: 14px; line-height: 1.2; }
</style>
</head>
<body>
<main class="sheet">
  <section class="card card--front" aria-label="Card front">
    <h1 class="company-name">Of Northfield, LLC</h1>
  </section>

  <section class="card card--back" aria-label="Card back">
    <header class="back__band">
      <h2 class="company-name">Of Northfield, LLC</h2>
    </header>

    <ul class="contact-list">
      <li>
        <svg viewBox="0 0 14 14" aria-hidden="true">
          <rect x="3" y="0.5" width="8" height="13" rx="1.2" fill="none" stroke="#111" stroke-width="1.2"/>
          <rect x="4.5" y="2" width="5" height="4" fill="#111"/>
          <rect x="4.5" y="7.5" width="5" height="4.5" fill="#111" opacity="0.7"/>
        </svg>
        <span>240-555-0187</span>
      </li>
      <li>
        <svg viewBox="0 0 14 14" aria-hidden="true">
          <rect x="0.5" y="3" width="13" height="8.5" fill="#111"/>
          <path d="M0.8 3.4 L7 8 L13.2 3.4" fill="none" stroke="#fff" stroke-width="1"/>
        </svg>
        <span>Fairhaven, MD 20811.</span>
      </li>
      <li>
        <svg viewBox="0 0 14 14" aria-hidden="true">
          <path d="M7 0.5 C4.2 0.5 2.5 2.5 2.5 4.8 C2.5 8 7 13.5 7 13.5 C7 13.5 11.5 8 11.5 4.8 C11.5 2.5 9.8 0.5 7 0.5 Z" fill="#111"/>
          <circle cx="7" cy="4.8" r="1.6" fill="#fff"/>
        </svg>
        <span>Dalep@wiremastersnorthfield.example</span>
      </li>
    </ul>

    <div class="person">
      <p class="person__name">Dale Pruitt</p>
      <p class="person__role">Electricians</p>
    </div>
  </section>
</main>
</body>
</html>
```